High-End Print/Digital Ad for Unique Luxury Travel Company Required

Objective:
Design a compelling and visually striking advertisement that highlights our company’s unmatched luxury travel experiences. The ad should elevate our brand image, spark curiosity, and drive prospective clients to contact us.
Target Audience:
• Affluent individuals seeking extraordinary, tailor-made travel experiences
• Affluent, luxury, high-net-worth individuals looking for value, expertise, and white-glove service
• Professionals or retirees who appreciate unique, thoughtfully curated travel over mainstream tourism
Key Messages to Communicate:
• One-of-a-kind luxury travel: Once-in-a-lifetime experiences that are curated with creativity and meticulous attention to detail
• Exceptional service: White-glove, personalized planning from start to finish
• 38 years’ travel experience – expert knowledge of destinations, modes of travel, premium accommodations and well-established, meaningful industry connections.
• Highly trusted: Cruise line executives often say, “No one does what you do.”
Tone and Style:
• Elegant, luxurious, sophisticated
• Eye-catching, polished, and modern
• Professional but warm—conveys trust and credibility
• High-impact visuals (full-bleed imagery, custom graphics, or high-end photography)
Deliverables:
• One full-page print ad and digital ad
• Ready-to-print, high-resolution file + working file (PSD, AI, etc.)
Optional: Social media-optimized version or short motion-graphic variation (if designer offers it)
Inspiration & Visual Style Suggestions:
• Think Lumen Voyages, Harrow Pike Wanderer, Silver Quill, or Orvel Retreats ad styles
• Large, emotive imagery with elegant typography
• Clean layout that speaks luxury, clarity, and trust
Copy Direction (draft):
For those who’ve explored the world—and crave something beyond the ordinary.
Each journey is a masterfully curated experience, rich in detail, seamless in execution, and unforgettable in every way.
Founded in 1997, Tidewell Journeys is a unique travel company specializing in cruising, all-inclusive luxury properties, and tours world-wide for individuals, groups, and incentives.
We offer an exceptional range of services designed to ensure every journey is flawlessly executed and truly unforgettable.
Let us help you plan your next extraordinary adventure.
Note: You may refine the copy slightly based on layout or format needs.
Other Resources for References:
1. Website - www.tidewelljourneys-example.com

```html
<!DOCTYPE html>
<html lang="en">
<head>
<meta charset="utf-8">
<title>Tidewell Journeys — Ad Campaign</title>
<link href="https://fonts.googleapis.com/css2?family=Montserrat:wght@300;400;500;700&display=swap" rel="stylesheet">
<style>
  :root {
    --board: #e0e0e0;
    --rule: #4a4a4a;
    --label: #3e3e3e;
    --white: #ffffff;
    --ink: #111111;
    --dusk-plum: #3d2a45;
    --dusk-teal: #2b7d8f;
    --sunset-orange: #e98a45;
    --sun-gold: #f8d35a;
    --sea-navy: #0f1a2e;
    --sea-deep: #080c18;
  }
  * { margin: 0; padding: 0; box-sizing: border-box; }
  html, body { width: 1200px; height: 800px; overflow: hidden; }
  body {
    position: relative;
    background: var(--board);
    font-family: "Montserrat", sans-serif;
  }

  .ad { position: absolute; overflow: hidden; }
  .ad__photo { position: absolute; inset: 0; }
  .ad__headline { position: absolute; font-weight: 700; letter-spacing: -0.01em; }
  .ad__subline { position: absolute; font-weight: 400; }
  .ad__brand {
    position: absolute;
    font-weight: 400;
    text-transform: uppercase;
    letter-spacing: 0.12em;
    color: var(--white);
    white-space: nowrap;
  }

  /* Print ad */
  .ad--print { left: 42px; top: 41px; width: 510px; height: 718px; color: var(--white); }
  .ad--print .ad__photo {
    background:
      linear-gradient(180deg, rgba(61,42,69,.95) 0%, rgba(43,125,143,.55) 14%, rgba(233,138,69,.85) 35%, rgba(248,211,90,.95) 58%, rgba(15,26,46,.95) 72%, var(--sea-deep) 100%),
      var(--dusk-plum);
  }
  .ad--print .ad__headline { left: 28px; top: 22px; font-size: 38px; line-height: 37px; }
  .ad--print .ad__subline { left: 28px; top: 173px; font-size: 18px; line-height: 20px; }
  .ad__body {
    position: absolute; right: 27px; top: 548px;
    font-size: 10.6px; line-height: 13.3px; text-align: right; font-weight: 400;
  }
  .ad__body p + p { margin-top: 14px; }
  .ad--print .ad__brand { right: 27px; top: 669px; font-size: 15px; }

  /* Digital banner */
  .ad--banner { left: 781px; top: 203px; width: 372px; height: 141px; color: var(--ink); }
  .ad--banner .ad__photo {
    background: linear-gradient(180deg, #e8874a 0%, #f6b459 35%, #fbd96a 62%, #d88a45 80%, #2b2436 100%);
  }
  .ad--banner .ad__headline { left: 11px; top: 24px; font-size: 20.5px; line-height: 21.5px; }
  .ad--banner .ad__subline { left: 11px; top: 90px; font-size: 10.5px; line-height: 12px; }
  .ad--banner .ad__brand { right: 10px; top: 120px; font-size: 8px; }

  /* Social media ad */
  .ad--social { left: 781px; top: 386px; width: 372px; height: 373px; color: var(--white); }
  .ad--social .ad__photo {
    background: linear-gradient(180deg, var(--dusk-plum) 0%, rgba(43,125,143,.9) 14%, var(--sunset-orange) 40%, var(--sun-gold) 62%, var(--sea-navy) 80%, var(--sea-deep) 100%);
  }
  .ad--social .ad__headline { left: 14px; top: 12px; font-size: 25.5px; line-height: 26.5px; }
  .ad--social .ad__subline { left: 14px; top: 91px; font-size: 12.5px; line-height: 14px; }
  .ad--social .ad__brand { right: 16px; top: 343px; font-size: 11px; }

  /* Board labels and connectors */
  .board-label {
    position: absolute; right: 47px;
    font-size: 15px; font-weight: 300; letter-spacing: 0.03em;
    color: var(--label); white-space: nowrap;
  }
  .board-label--print { top: 49px; }
  .board-label--social { top: 84px; }
  .board-label--banner { top: 118px; }
  .connectors { position: absolute; inset: 0; pointer-events: none; }
</style>
</head>
<body>

  <section class="ad ad--print">
    <div class="ad__photo" role="img" aria-label="Photograph of a luxury cruise ship bow at sea beneath a dramatic golden sunset sky"></div>
    <h1 class="ad__headline">For those<br>who’ve explored<br>the world</h1>
    <p class="ad__subline">and crave something<br>beyond the ordinary.</p>
    <div class="ad__body">
      <p>Each journey is a masterfully curated experience,<br>rich in detail, seamless in execution,<br>and unforgettable in every way.</p>
      <p>We offer an exceptional range of services<br>designed to ensure every journey is flawlessly<br>executed and truly unforgettable.<br>www.tidewelljourneys-example.com</p>
    </div>
    <div class="ad__brand">Tidewell Journeys</div>
  </section>

  <section class="ad ad--banner">
    <div class="ad__photo" role="img" aria-label="Photograph of a cruise ship sailing into a bright orange sunset"></div>
    <h2 class="ad__headline">For those<br>who’ve explored<br>the world</h2>
    <p class="ad__subline">and crave something<br>beyond the ordinary.</p>
    <div class="ad__brand">Tidewell Journeys</div>
  </section>

  <section class="ad ad--social">
    <div class="ad__photo" role="img" aria-label="Photograph of a luxury cruise ship at sea under a colourful sunset sky"></div>
    <h2 class="ad__headline">For those<br>who’ve explored<br>the world</h2>
    <p class="ad__subline">and crave something<br>beyond the ordinary.</p>
    <div class="ad__brand">Tidewell Journeys</div>
  </section>

  <div class="board-label board-label--print">PRINT AD</div>
  <div class="board-label board-label--social">SOCIAL MEDIA AD</div>
  <div class="board-label board-label--banner">DIGITAL BANNER AD</div>

  <svg class="connectors" width="1200" height="800" viewBox="0 0 1200 800" aria-hidden="true">
    <g fill="none" stroke="#4a4a4a" stroke-width="1">
      <line x1="564" y1="58.5" x2="1067" y2="58.5"/>
      <polyline points="999,93.5 699.5,93.5 699.5,398.5 767,398.5"/>
      <polyline points="980,127.5 735.5,127.5 735.5,221.5 767,221.5"/>
    </g>
    <g fill="#4a4a4a">
      <circle cx="564" cy="58.5" r="4.5"/>
      <circle cx="767" cy="398.5" r="4.5"/>
      <circle cx="767" cy="221.5" r="4.5"/>
    </g>
  </svg>

</body>
</html>
```